Heron Loan Partners Business Card

We need a business card design for our mortgage servicing company. In addition to servicing the loans of homeowners, we help homeowners with purchasing their homes and any mortgage refinancing. We would like to see designs that use the colors in the logo attached below (gold-ish yellow and navy blue), and any other design you deem fit! The design should communicate a simpler life with smart mortgages provided by Heron.

```html
<!DOCTYPE html>
<html lang="en">
<head>
<meta charset="utf-8">
<title>Heron Loan Partners – Business Card</title>
<link href="https://fonts.googleapis.com/css2?family=Montserrat:wght@400;500;700;800&display=swap" rel="stylesheet">
<style>
  :root {
    --gold: #e2b33b;
    --navy: #222055;
    --ink: #1a1a1a;
    --paper: #ffffff;
    --backdrop: #2b2b2d;
  }
  * { box-sizing: border-box; margin: 0; padding: 0; }
  html, body { width: 1200px; height: 880px; overflow: hidden; }
  body {
    background: var(--backdrop);
    font-family: "Montserrat", Arial, sans-serif;
    position: relative;
  }
  .card {
    position: absolute;
    width: 540px;
    height: 309px;
    background: var(--paper);
    overflow: hidden;
    box-shadow: 0 8px 24px rgba(0,0,0,.45);
  }
  .card--front { left: 40px; top: 120px; }
  .card--back { left: 620px; top: 450px; }

  .brand {
    display: flex;
    align-items: center;
    gap: 10px;
    color: var(--navy);
    font-weight: 800;
    white-space: nowrap;
  }
  .brand__dot {
    border-radius: 50%;
    background: var(--gold);
    flex: none;
  }
  .card--front .brand {
    position: absolute;
    left: 0; right: 0; top: 0; bottom: 0;
    justify-content: center;
    font-size: 34px;
    letter-spacing: .5px;
  }
  .card--front .brand__dot { width: 26px; height: 26px; }

  .card--back .brand {
    position: absolute;
    right: 40px; top: 46px;
    font-size: 20px;
  }
  .card--back .brand__dot { width: 16px; height: 16px; }

  .holder {
    position: absolute;
    left: 40px; top: 140px;
  }
  .holder__mark {
    position: absolute;
    left: -40px; top: 6px;
    width: 28px; height: 36px;
    background: var(--gold);
  }
  .holder__name {
    font-size: 17px;
    font-weight: 800;
    color: var(--navy);
    letter-spacing: .3px;
  }
  .holder__name span { color: var(--gold); }
  .holder__role {
    font-size: 13px;
    font-weight: 500;
    color: var(--ink);
    margin-top: 2px;
  }

  .address {
    position: absolute;
    right: 40px; top: 142px;
    text-align: right;
    font-size: 12px;
    font-weight: 500;
    line-height: 1.45;
    color: var(--ink);
  }

  .contacts {
    position: absolute;
    left: 40px; top: 196px;
    list-style: none;
    font-size: 12px;
    font-weight: 500;
    color: var(--ink);
  }
  .contacts li {
    display: flex;
    align-items: center;
    gap: 8px;
    height: 19px;
  }
  .contacts svg { width: 12px; height: 12px; flex: none; }

  .band {
    position: absolute;
    left: 0; bottom: 0;
    width: 540px; height: 309px;
    pointer-events: none;
  }
</style>
</head>
<body>

  <section class="card card--front" aria-label="Card front">
    <div class="brand"><span class="brand__dot"></span>Heron Loan Partners</div>
  </section>

  <section class="card card--back" aria-label="Card back">
    <svg class="band" viewBox="0 0 540 309" aria-hidden="true">
      <rect x="0" y="294" width="540" height="15" fill="var(--gold)"/>
      <rect x="0" y="276" width="200" height="11" fill="var(--gold)"/>
      <rect x="206" y="272" width="130" height="11" fill="var(--navy)"/>
      <polygon points="342,266 418,266 426,246 540,246 540,287 342,287" fill="var(--gold)"/>
      <polygon points="342,262 416,262 423,244 540,244 540,241 421,241 414,259 342,259" fill="var(--paper)"/>
    </svg>

    <div class="brand"><span class="brand__dot"></span>Heron Loan Partners</div>

    <div class="holder">
      <span class="holder__mark"></span>
      <p class="holder__name">DARA <span>WELLING</span></p>
      <p class="holder__role">Owner</p>
    </div>

    <p class="address">482 Linden Crest Ave, Ste<br>210, Dallas, TX 75208</p>

    <ul class="contacts">
      <li>
        <svg viewBox="0 0 24 24"><path fill="var(--gold)" d="M6.6 10.8a15.1 15.1 0 0 0 6.6 6.6l2.2-2.2a1 1 0 0 1 1-.25 11.4 11.4 0 0 0 3.6.57 1 1 0 0 1 1 1V20a1 1 0 0 1-1 1A17 17 0 0 1 3 4a1 1 0 0 1 1-1h3.5a1 1 0 0 1 1 1c0 1.25.2 2.45.57 3.6a1 1 0 0 1-.25 1z"/></svg>
        555.014.2290
      </li>
      <li>
        <svg viewBox="0 0 24 24"><rect x="2" y="5" width="20" height="14" rx="1.5" fill="var(--gold)"/><path d="M3 6l9 7 9-7" fill="none" stroke="#fff" stroke-width="1.6"/></svg>
        info@heronloanpartners.com
      </li>
      <li>
        <svg viewBox="0 0 24 24"><circle cx="12" cy="12" r="10" fill="var(--gold)"/><path d="M2 12h20M12 2c3 3 3 17 0 20M12 2c-3 3-3 17 0 20" fill="none" stroke="#fff" stroke-width="1.4"/></svg>
        www.heronloanpartners.com
      </li>
    </ul>
  </section>

</body>
</html>
```